Investment company needing business card

We are wanting a business card which looks sharp and easy on the eye. We are thinking of having a business card with the logo embossed on it, to really make it stand out. We will only have a small amount of information of the business card, person's name, position, email address and phone number

Contact Information for Business Card

Danielle Frost
Executive Assistant
+64 21 473 5162
danielf@harwickpartners.co.nz

Requirements
Must have
• Embossed logo
Should not have
• Not to be busy

```html
<!DOCTYPE html>
<html lang="en">
<head>
<meta charset="utf-8">
<title>Harwick Partners – Business Card</title>
<link rel="stylesheet" href="https://fonts.googleapis.com/css2?family=Lato:wght@400;700&display=swap">
<style>
  :root {
    --backdrop: #e4e4e4;
    --card-white: #ffffff;
    --card-dark: #262626;
    --card-dark-edge: #1f1f1f;
    --brand-green: #23b36f;
    --ink: #3a3a3a;
    --rule: #6a6a6a;
  }
  * { margin: 0; padding: 0; box-sizing: border-box; }
  html, body {
    width: 1200px;
    height: 900px;
    overflow: hidden;
    background: var(--backdrop);
    font-family: "Lato", sans-serif;
  }
  .canvas {
    position: relative;
    width: 1200px;
    height: 900px;
  }
  .card {
    position: absolute;
    top: 170px;
    width: 347px;
    height: 561px;
  }
  .card--front {
    left: 259px;
    background: var(--card-white);
  }
  .card--back {
    left: 631px;
    background: var(--card-dark);
    overflow: hidden;
  }
  .wordmark {
    position: absolute;
    left: 0;
    width: 100%;
    display: flex;
    align-items: center;
    justify-content: center;
    gap: 10px;
    font-weight: 700;
    color: var(--brand-green);
    letter-spacing: 0.5px;
    text-transform: uppercase;
  }
  .wordmark__square {
    width: 22px;
    height: 22px;
    background: var(--brand-green);
    flex: none;
  }
  .card--front .wordmark {
    top: 182px;
    font-size: 24px;
  }
  .card--back .wordmark {
    top: 460px;
    font-size: 28px;
  }
  .back-texture {
    position: absolute;
    inset: 0;
    background: linear-gradient(160deg, #2b2b2b 0%, var(--card-dark) 55%, var(--card-dark-edge) 100%);
  }
  .contact {
    position: absolute;
    left: 0;
    top: 382px;
    width: 100%;
    text-align: center;
    color: var(--ink);
  }
  .contact__name {
    font-size: 23px;
    font-weight: 700;
    color: var(--brand-green);
    letter-spacing: 0.5px;
    text-transform: uppercase;
    line-height: 28px;
  }
  .contact__role {
    font-size: 16px;
    line-height: 20px;
  }
  .contact__rule {
    width: 202px;
    height: 1px;
    background: var(--rule);
    margin: 17px auto 16px;
  }
  .contact__line {
    font-size: 16px;
    line-height: 22px;
  }
</style>
</head>
<body>
<main class="canvas">
  <section class="card card--front">
    <div class="wordmark">
      <span class="wordmark__square"></span>
      <span class="wordmark__name">Harwick Partners</span>
    </div>
    <div class="contact">
      <p class="contact__name">Danielle Frost</p>
      <p class="contact__role">Executive Assistant</p>
      <div class="contact__rule"></div>
      <p class="contact__line">+64 21 473 5162</p>
      <p class="contact__line">danielf@harwickpartners.co.nz</p>
    </div>
  </section>

  <section class="card card--back">
    <div class="back-texture" role="img" aria-label="Embossed repeating brand symbol pattern in dark grey"></div>
    <div class="wordmark">
      <span class="wordmark__name">Harwick Partners</span>
    </div>
  </section>
</main>
</body>
</html>
```